Banner ads for LP that work with same theme as below banners

Love the banner ads below. Need more with attached photos. But use the same wording, font as in below banner ads. Should be LP size 1200/627 so I can use for Pixorly and LP. Looking for great ads to use as LP ads. We do lots of ads so it will be worth your time to enter this contest you will be rewarded with a ton of work. Need several banner ads that work together. So maybe 1 of the dresses, 1 of the sweater, 1 of the leggings, 1 of the jacket

Target Market(s)

Women 24-45

Industry/Entity Type

Fashion

Requirements
Must have
• Banner ads that work for LP and Pixorly
Nice to have
• Several options to choose from
Should not have
• not sure

```html
<!DOCTYPE html>
<html lang="en">
<head>
<meta charset="UTF-8">
<title>Our Best Sweater Ever – Shop the Look</title>
<link rel="stylesheet" href="https://fonts.googleapis.com/css2?family=Kaushan+Script&family=Playfair+Display:wght@700&family=Libre+Baskerville&display=swap">
<style>
  :root {
    --wall-light: #f1f1f1;
    --wall-mid: #e2e4e6;
    --wall-cool: #d3d8dc;
    --ink: #3a3a3a;
    --paper: #ffffff;
    --hair: #b89b70;
    --sweater: #c8c8d4;
    --sweater-shade: #b4b4c2;
    --leggings: #2b2b2e;
  }
  * { margin: 0; padding: 0; box-sizing: border-box; }
  html, body { width: 1200px; height: 627px; overflow: hidden; }
  .banner {
    position: relative;
    width: 1200px;
    height: 627px;
    overflow: hidden;
    background: linear-gradient(90deg, var(--wall-light) 0%, var(--wall-mid) 45%, var(--wall-cool) 100%);
  }
  .model-photo {
    position: absolute;
    left: 205px;
    top: 0;
    width: 295px;
    height: 627px;
    border-radius: 40px 40px 0 0;
    background: linear-gradient(180deg,
      var(--hair) 0%,
      var(--hair) 22%,
      var(--sweater) 30%,
      var(--sweater-shade) 70%,
      var(--sweater) 92%,
      var(--leggings) 95%,
      var(--leggings) 100%);
  }
  .headline {
    position: absolute;
    left: 838px;
    top: 150px;
    width: 300px;
    text-align: center;
  }
  .headline-script {
    display: block;
    font-family: "Kaushan Script", cursive;
    font-size: 58px;
    line-height: 1;
    color: var(--paper);
  }
  .headline-product {
    display: block;
    font-family: "Playfair Display", serif;
    font-weight: 700;
    font-size: 50px;
    letter-spacing: 2px;
    line-height: 1;
    color: var(--ink);
    margin: 14px 0 8px 10px;
  }
  .headline-script.ever { margin-left: 20px; }
  .cta {
    position: absolute;
    left: 838px;
    top: 343px;
    width: 300px;
    height: 55px;
    background: var(--paper);
    display: flex;
    align-items: center;
    justify-content: center;
    font-family: "Libre Baskerville", serif;
    font-size: 24px;
    letter-spacing: 1.5px;
    color: var(--ink);
    text-decoration: none;
  }
</style>
</head>
<body>
  <main class="banner">
    <div class="model-photo" role="img" aria-label="Model with long wavy hair wearing an oversized lavender-grey knit turtleneck sweater and dark leggings, standing against a light wall"></div>
    <h1 class="headline">
      <span class="headline-script">Our Best</span>
      <span class="headline-product">SWEATER</span>
      <span class="headline-script ever">Ever!</span>
    </h1>
    <a class="cta" href="#">SHOP THE LOOK</a>
  </main>
</body>
</html>
```